creative pack design with extended budget for Zulimbo coffee product

- we need a packing design for a new product of coffee for our company Mireko Dasu located in Uganda.
- specialty Arabica coffee grown at slopes of Mountain Elgon with rich volcanic soils located in Eastern region of Uganda.
-  we have a logo already made and has registered in Uganda. our logo colors are mixture between a lot of brown color and yellow. vacuum  plastic bags.
- there is no restrictions towards your imagination .
-  all details available
- we will launch our product through phases ;
- phase 1 is  a ground coffee : ( Turkish coffee )  2 degrees of roasting which are ( medium dark , light ) of 250 grm
b) roasted beans: 2 degrees ( medium, dark) of 250 grm & 1000 grm
- we need also to highlight the eastern spirit of Turkish coffee
- we  need designs, the info and color only will be changed depending on previous classifications

Target Market(s)
Arab countries, Turkey , Uganda, Europe
Colors
Designer to choose colors to be used in the design.
Requirements
Nice to have
- about nature , Elgon mountain , farmers, freshness, distinctive product, soul of east such as decorated cup of Turkish coffee . these just an ideas but there is no restrictions on your imagination

```html
<!DOCTYPE html>
<html lang="en">
<head>
<meta charset="utf-8">
<title>Zulimbo Arabica Coffee – Pack Range</title>
<link rel="stylesheet" href="https://fonts.googleapis.com/css2?family=Allura&family=Montserrat:wght@500;600;700&display=swap">
<style>
  :root {
    --canvas: #ffffff;
    --label: #f7f7f8;
    --ink: #2b2f4a;
    --illustration-light: #f4f4f5;
    --illustration-mid: #e4e4e6;

    --rose-side: #b8658f;
    --rose-front: #3f1d40;
    --rose-accent: #a04f8f;
    --rose-strip: #b66a93;

    --jade-side: #1fa58e;
    --jade-front: #1f2a2d;
    --jade-accent: #25b49b;
    --jade-strip: #1f9e87;
    --jade-word: #c6a52a;

    --violet-side: #8b52d1;
    --violet-front: #28214f;
    --violet-accent: #9b5ad3;
    --violet-strip: #9a6fd0;
  }

  * { box-sizing: border-box; margin: 0; padding: 0; }

  html, body {
    width: 1200px;
    height: 1200px;
    overflow: hidden;
    background: var(--canvas);
  }

  .range {
    width: 1200px;
    height: 1200px;
    display: flex;
    justify-content: center;
    align-items: center;
    gap: 60px;
  }

  .pack {
    display: flex;
    width: 320px;
    height: 640px;
  }

  .pack__gusset {
    width: 90px;
    background: var(--side);
  }

  .pack__front {
    width: 230px;
    background: var(--front);
    position: relative;
  }

  .pack__seal {
    position: absolute;
    top: 0; left: 0; right: 0;
    height: 22px;
    background: repeating-linear-gradient(90deg, rgba(255,255,255,0.10) 0 2px, transparent 2px 5px);
  }

  .label {
    position: absolute;
    top: 130px;
    left: 14px;
    right: 14px;
    bottom: 60px;
    background: var(--label);
    display: flex;
    flex-direction: column;
    align-items: center;
  }

  .brand {
    position: absolute;
    top: -46px;
    width: 120px;
    height: 120px;
    border-radius: 50%;
    background: var(--label);
    display: flex;
    align-items: center;
    justify-content: center;
  }

  .brand__name {
    font-family: "Montserrat", sans-serif;
    font-weight: 700;
    font-size: 16px;
    letter-spacing: 1px;
    color: var(--front);
    text-transform: uppercase;
  }

  .product-name {
    margin-top: 80px;
    text-align: center;
    line-height: 1;
    font-weight: normal;
  }

  .product-name__script {
    display: block;
    font-family: "Allura", cursive;
    font-size: 46px;
    color: var(--accent);
  }

  .product-name__word {
    display: block;
    font-family: "Montserrat", sans-serif;
    font-weight: 600;
    font-size: 16px;
    letter-spacing: 1px;
    color: var(--word, var(--ink));
    margin-top: -2px;
    padding-left: 40px;
  }

  .illustration {
    margin-top: 16px;
    width: 176px;
    height: 200px;
    border-radius: 6px;
    background: linear-gradient(180deg, var(--illustration-light) 0%, var(--illustration-mid) 55%, var(--illustration-light) 100%);
    opacity: 0.8;
  }

  .info-strip {
    position: absolute;
    left: 0; right: 0; bottom: 0;
    height: 30px;
    background: var(--strip);
    display: flex;
    justify-content: space-between;
    align-items: center;
    padding: 0 12px;
    font-family: "Montserrat", sans-serif;
    font-weight: 500;
    font-size: 11px;
    color: #ffffff;
  }

  .pack--rose   { --side: var(--rose-side);   --front: var(--rose-front);   --accent: var(--rose-accent);   --strip: var(--rose-strip); }
  .pack--jade   { --side: var(--jade-side);   --front: var(--jade-front);   --accent: var(--jade-accent);   --strip: var(--jade-strip); --word: var(--jade-word); }
  .pack--violet { --side: var(--violet-side); --front: var(--violet-front); --accent: var(--violet-accent); --strip: var(--violet-strip); }
</style>
</head>
<body>
<main class="range">

  <article class="pack pack--rose">
    <div class="pack__gusset" role="img" aria-label="Ornamental rose pattern on side gusset"></div>
    <div class="pack__front">
      <div class="pack__seal"></div>
      <div class="label">
        <div class="brand"><span class="brand__name">Zulimbo</span></div>
        <h2 class="product-name">
          <span class="product-name__script">Arabica</span>
          <span class="product-name__word">COFFEE</span>
        </h2>
        <div class="illustration" role="img" aria-label="Fine line illustration of a coffee farmer among mountains and coffee branches"></div>
        <div class="info-strip"><span>ground coffee</span><span>250 grama</span></div>
      </div>
    </div>
  </article>

  <article class="pack pack--jade">
    <div class="pack__gusset" role="img" aria-label="Ornamental jade pattern on side gusset"></div>
    <div class="pack__front">
      <div class="pack__seal"></div>
      <div class="label">
        <div class="brand"><span class="brand__name">Zulimbo</span></div>
        <h2 class="product-name">
          <span class="product-name__script">Arabica</span>
          <span class="product-name__word">COFFEE</span>
        </h2>
        <div class="illustration" role="img" aria-label="Fine line illustration of a coffee farmer among mountains and coffee branches"></div>
        <div class="info-strip"><span>ground coffee</span><span>250 grama</span></div>
      </div>
    </div>
  </article>

  <article class="pack pack--violet">
    <div class="pack__gusset" role="img" aria-label="Ornamental violet pattern on side gusset"></div>
    <div class="pack__front">
      <div class="pack__seal"></div>
      <div class="label">
        <div class="brand"><span class="brand__name">Zulimbo</span></div>
        <h2 class="product-name">
          <span class="product-name__script">Arabica</span>
          <span class="product-name__word">COFFEE</span>
        </h2>
        <div class="illustration" role="img" aria-label="Fine line illustration of a coffee farmer among mountains and coffee branches"></div>
        <div class="info-strip"><span>ground coffee</span><span>250 grama</span></div>
      </div>
    </div>
  </article>

</main>
</body>
</html>
```